Machining Business Order Thank You Insert

I am looking for a business style card to include with orders that I ship. The card needs to thank the recipient for their order, and encourage them to leave a review. The card should include my business name and contact information and have an area to hand write a message.

I mainly sale on Craftlane and my own website. We are a machining an manufacturing business that are in the sale of mostly metal machined and 3d printed plastic products.

The front of the card should include the following:
Logo: (attached)
Snapgram: https://www.snapgram.example/kelvomill/
Friendsbook: https://www.friendsbook.example/KelvoMill
Website: https://www.kelvomill.example/

The back of the card needs an area to write a message

Industry/Entity Type

3D Printing, Machining, Craftlane

Contact Information for Business Card

Black or white front, white back to write a personal message

Font styles to use
Sans Serif

Colors

Designer to choose colors to be used in the design.

Requirements
Must have
• Encourage a review, social media info

```html
<!DOCTYPE html>
<html lang="en">
<head>
<meta charset="UTF-8">
<title>KelvoMill Order Thank You Card</title>
<link href="https://fonts.googleapis.com/css2?family=Montserrat:wght@500;600;700&display=swap" rel="stylesheet">
<style>
  :root {
    --orange: #f15a29;
    --grey: #6d6e71;
    --ink: #3a3b48;
    --paper: #ffffff;
    --rule: #c9cacc;
    --write-line: #d8d9db;
  }
  * { margin: 0; padding: 0; box-sizing: border-box; }
  html, body { width: 1200px; height: 2666px; overflow: hidden; background: var(--paper); }
  body { position: relative; font-family: "Montserrat", Arial, sans-serif; }

  .card {
    position: absolute;
    left: 140px;
    width: 920px;
    height: 525px;
    background: var(--paper);
    box-shadow: 0 6px 22px rgba(0,0,0,0.28);
    overflow: hidden;
  }
  .card--message { top: 1255px; }
  .card--contact { top: 1886px; }

  .brand { position: absolute; display: flex; align-items: center; gap: 18px; }
  .brand__mark { background: var(--orange); flex: none; }
  .brand__name { font-weight: 600; color: var(--grey); letter-spacing: 0.22em; line-height: 1; white-space: nowrap; }

  /* Message side */
  .card--message .brand { left: 0; right: 0; top: 48px; justify-content: center; }
  .card--message .brand__mark { width: 28px; height: 28px; }
  .card--message .brand__name { font-size: 36px; }

  .thanks {
    position: absolute; left: 0; right: 0; top: 118px;
    text-align: center;
    font-size: 36px; font-weight: 700; color: var(--orange); line-height: 1;
  }
  .write-area { position: absolute; left: 90px; right: 90px; top: 190px; }
  .write-area__line { height: 52px; border-bottom: 2px solid var(--write-line); }
  .review-note {
    position: absolute; left: 0; right: 0; top: 440px;
    text-align: center;
    font-size: 21px; font-weight: 500; color: var(--ink); line-height: 1.3;
  }
  .review-note strong { color: var(--orange); font-weight: 600; }

  /* Contact side */
  .card--contact .brand { left: 64px; top: 250px; }
  .card--contact .brand__mark { width: 28px; height: 28px; }
  .card--contact .brand__name { font-size: 36px; }

  .divider { position: absolute; left: 460px; top: 100px; width: 1px; height: 280px; background: var(--rule); }

  .contact { position: absolute; left: 508px; top: 108px; }
  .contact__name { font-size: 45px; font-weight: 700; color: var(--ink); line-height: 1; }
  .contact__role { margin-top: 12px; font-size: 25px; font-weight: 600; color: var(--orange); line-height: 1; }
  .contact__list { list-style: none; margin-top: 48px; }
  .contact__item {
    display: flex; align-items: center; gap: 22px;
    height: 44px; margin-bottom: 13px;
    font-size: 23px; font-weight: 500; color: var(--ink); white-space: nowrap;
  }
  .contact__icon {
    width: 44px; height: 44px; border-radius: 50%;
    background: var(--orange); flex: none;
    display: flex; align-items: center; justify-content: center;
  }

  .footer-bands { position: absolute; left: 0; bottom: 0; width: 920px; height: 40px; }
</style>
</head>
<body>

  <section class="card card--message" aria-label="Card message side">
    <div class="brand">
      <span class="brand__mark"></span>
      <span class="brand__name">KELVOMILL</span>
    </div>
    <p class="thanks">Thank you for your order!</p>
    <div class="write-area" aria-label="Space for a handwritten message">
      <div class="write-area__line"></div>
      <div class="write-area__line"></div>
      <div class="write-area__line"></div>
      <div class="write-area__line"></div>
    </div>
    <p class="review-note">Enjoying your order? Please leave us a review on <strong>Craftlane</strong></p>
  </section>

  <section class="card card--contact" aria-label="Card contact side">
    <div class="brand">
      <span class="brand__mark"></span>
      <span class="brand__name">KELVOMILL</span>
    </div>

    <div class="divider"></div>

    <div class="contact">
      <p class="contact__name">Lorem Ipsum</p>
      <p class="contact__role">Lorem Ipsum is simply</p>
      <ul class="contact__list">
        <li class="contact__item">
          <span class="contact__icon">
            <svg width="26" height="26" viewBox="0 0 26 26" fill="none" stroke="#fff" stroke-width="2">
              <circle cx="13" cy="13" r="10"/>
              <ellipse cx="13" cy="13" rx="4.5" ry="10"/>
              <line x1="3" y1="13" x2="23" y2="13"/>
            </svg>
          </span>
          www.kelvomill.example
        </li>
        <li class="contact__item">
          <span class="contact__icon">
            <svg width="24" height="24" viewBox="0 0 24 24" fill="none" stroke="#fff" stroke-width="2.2" stroke-linecap="round">
              <path d="M10 14a4 4 0 0 0 5.7 0l3-3a4 4 0 0 0-5.7-5.7l-1 1"/>
              <path d="M14 10a4 4 0 0 0-5.7 0l-3 3a4 4 0 0 0 5.7 5.7l1-1"/>
            </svg>
          </span>
          www.snapgram.example
        </li>
        <li class="contact__item">
          <span class="contact__icon">
            <svg width="24" height="24" viewBox="0 0 24 24" fill="none" stroke="#fff" stroke-width="2.2" stroke-linejoin="round">
              <path d="M4 5h16v11H10l-5 4v-4H4z"/>
            </svg>
          </span>
          www.friendsbook.example
        </li>
      </ul>
    </div>

    <svg class="footer-bands" viewBox="0 0 920 40" aria-hidden="true">
      <path d="M0 5 H355 Q385 5 405 40 H0 Z" fill="var(--grey)"/>
      <path d="M395 21 H920 V40 H408 Q403 29 395 21 Z" fill="var(--orange)"/>
    </svg>
  </section>

</body>
</html>
```